Need Help having my business card stand out

I am the owner of Birchway Canine Training and would like for my business cards to stand out. I have been trying to keep designing them myself but I can't get what I have in my head on the card. I will try my best to post templates that I like for inspirations. I want something unique but elegant. I don't want in to look cartoony or cheesy. It needs to pop in a pet shop but also in a coffee shop or gym.

Target Market(s)

Dog owners, Married ,No young kids Jr High school kids and up (maybe kids on the way) Executives, Stay at home moms/wives, Small business owners

Industry/Entity Type

Dog Training

Contact Information for Business Card

Lowell Spratt, 281-904-3376, info@birchwaycanine.example, www.birchwaycanine.example

Colors

Designer to choose colors to be used in the design.

Requirements
Must have
• my logo
Should not have
• Cursive lettering

```html
<!DOCTYPE html>
<html lang="en">
<head>
<meta charset="utf-8">
<title>Birchway Canine Training — Business Card</title>
<link rel="stylesheet" href="https://fonts.googleapis.com/css2?family=Open+Sans:ital,wght@0,400;0,600;0,700;1,600;1,800&family=Quicksand:wght@500&display=swap">
<style>
  :root {
    --stage: #5f5f5f;
    --card: #050505;
    --dot-tone: #3a3a3a;
    --logo-grey: #6e6e6e;
    --tag-grey: #8a8a8a;
    --green: #1fc45f;
    --white: #ffffff;
  }
  * { box-sizing: border-box; margin: 0; padding: 0; }
  html, body {
    width: 1200px; height: 900px; overflow: hidden;
    background: var(--stage);
    font-family: "Open Sans", Arial, sans-serif;
  }
  .stage { position: relative; width: 1200px; height: 900px; }

  .card {
    position: absolute; left: 250px;
    width: 700px; height: 400px;
    background: var(--card);
    overflow: hidden;
    box-shadow: 0 14px 30px rgba(0,0,0,.45);
  }
  .card--front { top: 35px; }
  .card--back  { top: 465px; }

  .halftone { position: absolute; }
  .card--front .halftone--top-right {
    right: 0; top: 0; width: 300px; height: 125px;
    background: radial-gradient(ellipse at 70% 30%, #4a4a4a 0%, #262626 55%, transparent 100%);
  }
  .card--front .halftone--bottom-left {
    left: 0; top: 125px; width: 330px; height: 275px;
    background: radial-gradient(ellipse at 20% 80%, #3f3f3f 0%, #1e1e1e 60%, transparent 100%);
  }
  .card--back .halftone--top-right {
    right: 0; top: 0; width: 300px; height: 150px;
    background: radial-gradient(ellipse at 80% 30%, #4a4a4a 0%, #222 55%, transparent 100%);
  }
  .card--back .halftone--bottom-left {
    left: 0; top: 155px; width: 330px; height: 245px;
    background: radial-gradient(ellipse at 15% 85%, #474747 0%, #1e1e1e 60%, transparent 100%);
  }

  .brand-name {
    position: absolute;
    font-weight: 600;
    color: var(--logo-grey);
    text-align: center;
    line-height: 1.05;
  }
  .card--front .brand-name {
    left: 220px; top: 95px; width: 300px;
    font-size: 38px; letter-spacing: .5px;
  }
  .card--back .brand-name {
    right: 40px; top: 45px; width: 200px;
    font-size: 22px;
  }

  .tagline {
    position: absolute; right: 30px; top: 270px;
    font-family: "Quicksand", "Open Sans", sans-serif;
    font-size: 18px; letter-spacing: .8px;
    color: var(--tag-grey);
    display: flex; align-items: center; gap: 10px;
  }
  .tagline .sep {
    width: 6px; height: 6px; border-radius: 50%;
    background: var(--green);
  }

  .holder { position: absolute; left: 100px; top: 120px; }
  .holder__name { font-size: 26px; color: var(--white); font-weight: 400; }
  .holder__name b { font-weight: 800; font-style: italic; }
  .holder__role {
    font-size: 17px; color: var(--green);
    font-weight: 600; font-style: italic; margin-top: 2px;
  }

  .divider {
    position: absolute; left: 340px; top: 130px;
    width: 2px; height: 270px; background: var(--green);
  }

  .contacts {
    position: absolute; left: 375px; top: 220px;
    list-style: none; color: var(--white); font-size: 16px;
  }
  .contacts li { display: flex; align-items: center; gap: 10px; height: 32px; }
  .contacts svg { width: 17px; height: 17px; flex: none; fill: var(--green); }
</style>
</head>
<body>
<main class="stage">

  <section class="card card--front" aria-label="Card front">
    <div class="halftone halftone--top-right" role="img" aria-label="Fading halftone dot pattern"></div>
    <div class="halftone halftone--bottom-left" role="img" aria-label="Fading halftone dot pattern"></div>
    <div class="brand-name">Birchway Canine Training</div>
    <div class="tagline">
      <span>come</span><span class="sep"></span>
      <span>sit</span><span class="sep"></span>
      <span>down</span><span class="sep"></span>
      <span>stay</span><span class="sep"></span>
      <span>good</span>
    </div>
  </section>

  <section class="card card--back" aria-label="Card back">
    <div class="halftone halftone--top-right" role="img" aria-label="Fading halftone dot pattern"></div>
    <div class="halftone halftone--bottom-left" role="img" aria-label="Fading halftone dot pattern"></div>
    <div class="brand-name">Birchway Canine Training</div>

    <div class="holder">
      <p class="holder__name"><b>Lowell</b> Spratt</p>
      <p class="holder__role">Designation</p>
    </div>

    <div class="divider"></div>

    <ul class="contacts">
      <li>
        <svg viewBox="0 0 24 24"><path d="M12 2a7 7 0 0 0-7 7c0 5 7 13 7 13s7-8 7-13a7 7 0 0 0-7-7zm0 9.5A2.5 2.5 0 1 1 12 6.5a2.5 2.5 0 0 1 0 5z"/></svg>
        <span>000 Larch Hollow Rd., Suite 300, Fenwick, US 0000</span>
      </li>
      <li>
        <svg viewBox="0 0 24 24"><path d="M3 9c0-2 4-4 9-4s9 2 9 4v2h-5V9H8v2H3zM6 12h12l2 7H4zm6 1.5a2.5 2.5 0 1 0 0 5 2.5 2.5 0 0 0 0-5z"/></svg>
        <span>281-904-3376</span>
      </li>
      <li>
        <svg viewBox="0 0 24 24"><path d="M7 3h10v5H7zM3 9h18v11H3zm3 3v2h12v-2zm0 4v2h8v-2z"/></svg>
        <span>281-904-3377</span>
      </li>
      <li>
        <svg viewBox="0 0 24 24"><path d="M2 5h20v14H2zm2 2v.5l8 5.5 8-5.5V7zm0 3v7h16v-7l-8 5.5z"/></svg>
        <span>info@birchwaycanine.example</span>
      </li>
      <li>
        <svg viewBox="0 0 24 24"><path d="M12 2a10 10 0 1 0 0 20 10 10 0 0 0 0-20zm6.9 9h-3a15 15 0 0 0-1.3-6A8 8 0 0 1 18.9 11zM12 4c.9 1.3 1.7 3.8 1.9 7h-3.8C10.3 7.8 11.1 5.3 12 4zM9.4 5a15 15 0 0 0-1.3 6h-3A8 8 0 0 1 9.4 5zM5.1 13h3a15 15 0 0 0 1.3 6A8 8 0 0 1 5.1 13zM12 20c-.9-1.3-1.7-3.8-1.9-7h3.8c-.2 3.2-1 5.7-1.9 7zm2.6-1a15 15 0 0 0 1.3-6h3a8 8 0 0 1-4.3 6z"/></svg>
        <span>www.birchwaycanine.example</span>
      </li>
    </ul>
  </section>

</main>
</body>
</html>
```